Business card for denture clinic Veltrimora

We need a new business card with our new logo. We are a denture clinic in New Zealand with our target market being 45+ years old. We would need a space on the back to write our patients next appointment on. We would space for only one appointment rather than a list. We will attach a photo showing an example of this. But of course, we would like to see your twist on this. We want it to be bold and easy to read and a good mixture of professional but modern. We have attached our logo to be used on the card.

Target Market(s)

People aged 45+ needing dentures

Industry/Entity Type

Dental

Contact Information for Business Card

We want our logo on the front and the space to write an appointment on the back. I've attached an example our our old business card showing this. We need to have the technicians details on the front.

Font styles to use
Sans Serif

Colors
0255a3
919191
fbfbfb

Requirements
Must have
• The following details:
• Liam Dorsett BDT, PGDipCDentTech Calverin
• Dental Prosthetist
• Phone numbers: 0800 47 3125
• 09 572 1394
• Email: liam@veltrimora.co.nz
• www.veltrimora.co.nz
• Address: 14 Marlow Crest Road
• Halbrook West
• Auckland 0793
Nice to have
• We would like our business cards to have more than just two colours as we want them to be more vibrant. We have uploaded an example of a business card we liked that showed this.

```html
<!DOCTYPE html>
<html lang="en">
<head>
<meta charset="utf-8">
<title>Veltrimora Business Card</title>
<link rel="stylesheet" href="https://fonts.googleapis.com/css2?family=Open+Sans:wght@400;600;700&display=swap">
<style>
  :root {
    --brand-blue: #0a66ad;
    --brand-blue-deep: #0255a3;
    --teal: #13938b;
    --orange: #e06a35;
    --navy: #173340;
    --paper: #ffffff;
    --grey-text: #919191;
    --backdrop-light: #a3a3a3;
    --backdrop-dark: #8e8e8e;
    --rule: #8a8f96;
  }
  * { margin: 0; padding: 0; box-sizing: border-box; }
  html, body { width: 1200px; height: 900px; overflow: hidden; }
  body {
    position: relative;
    background: linear-gradient(180deg, var(--backdrop-light), var(--backdrop-dark));
    font-family: "Open Sans", Arial, sans-serif;
  }
  .card {
    position: absolute;
    top: 170px;
    width: 347px;
    height: 561px;
    background: var(--paper);
    overflow: hidden;
  }
  .card--front { left: 259px; }
  .card--back { left: 631px; }

  .brand-mark { position: absolute; background: var(--brand-blue); }
  .brand-name {
    position: absolute;
    left: 0; width: 100%;
    text-align: center;
    font-weight: 600;
    letter-spacing: 3px;
    line-height: 1;
  }
  .brand-web {
    position: absolute;
    left: 0; width: 100%;
    text-align: center;
    font-size: 13px;
    letter-spacing: 1.5px;
    line-height: 1;
  }

  /* Front */
  .card--front .brand-mark { left: 146px; top: 105px; width: 55px; height: 53px; }
  .card--front .brand-name { top: 166px; font-size: 25px; color: var(--brand-blue); }
  .card--front .brand-web { top: 194px; color: var(--grey-text); }
  .front-shapes { position: absolute; left: 0; top: 0; }
  .contact {
    position: absolute;
    left: 19px;
    color: var(--paper);
    font-size: 15px;
    line-height: 20.5px;
  }
  .contact--lines { top: 334px; }
  .contact--address { top: 407px; }
  .technician {
    position: absolute;
    right: 24px;
    top: 475px;
    text-align: right;
    color: var(--paper);
  }
  .technician__name { font-size: 20px; font-weight: 600; line-height: 24px; }
  .technician__name small { font-size: 15px; margin-left: 4px; }
  .technician__quals { font-size: 16px; font-weight: 600; line-height: 22px; }
  .technician__role { font-size: 15px; margin-top: 6px; }

  /* Back */
  .back-header {
    position: absolute;
    left: 0; top: 0;
    width: 100%; height: 280px;
    background: var(--brand-blue);
  }
  .card--back .brand-mark { left: 144px; top: 70px; width: 60px; height: 58px; background: var(--paper); }
  .card--back .brand-name { top: 136px; font-size: 27px; color: var(--paper); }
  .card--back .brand-web { top: 167px; color: var(--paper); }
  .appointment-title {
    position: absolute;
    left: 0; width: 100%; top: 348px;
    text-align: center;
    font-size: 20px;
    font-weight: 700;
    letter-spacing: 0.3px;
    color: var(--brand-blue-deep);
  }
  .appointment-field {
    position: absolute;
    left: 43px;
    width: 263px;
    display: flex;
    align-items: center;
    font-size: 18px;
    font-weight: 700;
    color: var(--brand-blue-deep);
  }
  .appointment-field--date { top: 429px; }
  .appointment-field--time { top: 477px; }
  .appointment-field span { width: 66px; }
  .appointment-field i { flex: 1; border-top: 1.5px solid var(--rule); }
</style>
</head>
<body>
  <section class="card card--front" aria-label="Business card front">
    <div class="brand-mark"></div>
    <div class="brand-name">VELTRIMORA</div>
    <div class="brand-web">www.veltrimora.co.nz</div>
    <svg class="front-shapes" width="347" height="561" viewBox="0 0 347 561">
      <polygon points="0,237 286,367 0,561" fill="var(--teal)"/>
      <polygon points="286,367 313,402 0,561" fill="var(--orange)"/>
      <polygon points="0,561 347,383 347,561" fill="var(--navy)"/>
    </svg>
    <div class="contact contact--lines">
      P: 0800 47 3125<br>
      P: 09 572 1394<br>
      E: liam@veltrimora.co.nz
    </div>
    <div class="contact contact--address">
      14 Marlow Crest Road<br>
      Halbrook West<br>
      Auckland 0793
    </div>
    <div class="technician">
      <div class="technician__name">LIAM DORSETT<small>BDT,</small></div>
      <div class="technician__quals">PG DIP DENT TECH CALVERIN</div>
      <div class="technician__role">Dental Prosthetist</div>
    </div>
  </section>

  <section class="card card--back" aria-label="Business card back">
    <div class="back-header"></div>
    <div class="brand-mark"></div>
    <div class="brand-name">VELTRIMORA</div>
    <div class="brand-web">www.veltrimora.co.nz</div>
    <div class="appointment-title">YOUR NEXT APPOINTMENT</div>
    <div class="appointment-field appointment-field--date"><span>DATE</span><i></i></div>
    <div class="appointment-field appointment-field--time"><span>TIME</span><i></i></div>
  </section>
</body>
</html>
```